Business Card Design

New business card design

Target Market(s)

Residential & Commercial Property Managers

Industry/Entity Type

Plumbing Services

Contact Information for Business Card

Name - Rowan Keddle, title - Director, Phone Number - 0431 286 517, email - rowan@tbk-plumbing.com.au, Company ABN - 73 215 904 386,

Font styles to use
Sans Serif

Colors
0054AA
0677BA
7BADD7
CADEEF
E8F1F8

```html
<!DOCTYPE html>
<html lang="en">
<head>
<meta charset="utf-8">
<title>TBK Plumbing Services – Business Card</title>
<link rel="stylesheet" href="https://fonts.googleapis.com/css2?family=Montserrat:wght@400;500;700&display=swap">
<style>
  :root {
    --backdrop: #232323;
    --card-white: #ffffff;
    --brand-blue: #2aa8e0;
    --brand-deep: #0677ba;
    --brand-light: #7badd7;
    --brand-pale: #cadeef;
    --ink: #1d2329;
    --on-blue: #ffffff;
  }
  html, body {
    margin: 0;
    padding: 0;
    width: 1200px;
    height: 780px;
    overflow: hidden;
    background: var(--backdrop);
    font-family: "Montserrat", sans-serif;
  }
  .canvas {
    position: relative;
    width: 1200px;
    height: 780px;
    display: flex;
    align-items: center;
    justify-content: center;
    gap: 40px;
  }
  .card {
    width: 540px;
    height: 310px;
    display: block;
    filter: drop-shadow(0 10px 18px rgba(0,0,0,0.45));
  }
  .card-front .wave-band { fill: var(--brand-blue); }
  .card-front .wave-rule { fill: none; stroke: var(--card-white); stroke-width: 2.5; }
  .card-front .divider { fill: none; stroke: var(--on-blue); stroke-width: 1.4; }
  .brand-name {
    font-family: "Montserrat", sans-serif;
    font-weight: 500;
    font-size: 25px;
    fill: var(--ink);
    letter-spacing: 0.3px;
  }
  .brand-dot { fill: var(--brand-blue); }
  .person-name { font-weight: 700; font-size: 21px; fill: var(--on-blue); }
  .person-title { font-weight: 400; font-size: 14px; fill: var(--on-blue); }
  .contact-line { font-weight: 400; font-size: 13.5px; fill: var(--on-blue); }
  .company-abn { font-weight: 400; font-size: 13px; fill: var(--on-blue); }
  .icon { fill: none; stroke: var(--on-blue); stroke-width: 1.5; stroke-linecap: round; stroke-linejoin: round; }
</style>
</head>
<body>
<main class="canvas">

  <svg class="card card-back" viewBox="0 0 540 310" role="img" aria-label="Card back: repeating pattern of water droplets in light and deep blue">
    <defs>
      <linearGradient id="back-fill" x1="0" y1="0" x2="1" y2="0">
        <stop offset="0" stop-color="#5cc2ef"/>
        <stop offset="0.5" stop-color="var(--brand-blue)"/>
        <stop offset="1" stop-color="var(--brand-deep)"/>
      </linearGradient>
    </defs>
    <rect class="back-surface" width="540" height="310" rx="22" fill="url(#back-fill)"/>
  </svg>

  <svg class="card card-front" viewBox="0 0 540 310">
    <defs>
      <clipPath id="front-shape"><rect width="540" height="310" rx="22"/></clipPath>
    </defs>
    <g clip-path="url(#front-shape)">
      <rect class="front-surface" width="540" height="310" fill="var(--card-white)"/>
      <path class="wave-band" d="M0,214 C140,160 300,150 415,122 C485,104 522,80 540,52 L540,310 L0,310 Z"/>
      <path class="wave-rule" d="M0,204 C140,150 300,140 412,112 C480,95 518,72 536,44"/>
    </g>

    <g class="brand-lockup">
      <circle class="brand-dot" cx="134" cy="80" r="7.5"/>
      <text class="brand-name" x="150" y="89">TBK Plumbing Services</text>
    </g>

    <g class="contact-block">
      <text class="person-name" x="24" y="230">Rowan Keddle</text>
      <text class="person-title" x="24" y="248">Director</text>

      <path class="divider" d="M22,256 L250,256 L268,240 L518,240"/>

      <text class="company-abn" x="518" y="259" text-anchor="end">Company ABN - 73 215 904 386</text>

      <g class="icon phone-icon" transform="translate(24,264)">
        <path d="M2,1.5 L4.5,1 L6,4.5 L4.5,5.8 C5.3,7.6 6.6,8.9 8.4,9.7 L9.7,8.2 L13,9.6 L12.6,12.2 C7,12.5 1.6,7.2 2,1.5 Z"/>
      </g>
      <text class="contact-line" x="44" y="276">0431 286 517</text>

      <g class="icon mail-icon" transform="translate(24,282)">
        <rect x="0.5" y="1.5" width="13" height="9" rx="1"/>
        <path d="M0.8,2 L7,7 L13.2,2"/>
      </g>
      <text class="contact-line" x="44" y="293">rowan@tbk-plumbing.com.au</text>
    </g>
  </svg>

</main>
</body>
</html>
```